Veltrane Group Business Card Design

The CEO is looking for a new trendy look for his business card.
You can stay with current branding or come up with something new/creative. It can be 3D, including Medical Office buildings. You can use our logo in a variety of colors. Please include name, title, company name, company website, email address, cell number

Target Market(s)

Real Estate Development and Construction

Industry/Entity Type

Health care real estate

Contact Information for Business Card

Rohesh Kamdar, CEO M-604.781.2249 E-roheshkamdar@veltrane.com Address:4180 Lindqvist Ave, Brennick, OH 44812 www.veltrane.com

Font styles to use
Other font styles liked:
• Be creative

Requirements
Must have
• Creative, trendy look
Nice to have
• Please go to our website to get a feel- www. veltrane.com
Should not have
• small fonts

```html
<!DOCTYPE html>
<html lang="en">
<head>
<meta charset="utf-8">
<title>Veltrane Group – Business Card</title>
<link href="https://fonts.googleapis.com/css2?family=Archivo+Black&family=Roboto+Slab:wght@400&display=swap" rel="stylesheet">
<style>
  :root{
    --stage:#1c1c1c;
    --card-black:#161616;
    --mark-grey:#b9b9b9;
    --white:#ffffff;
    --brand-red:#b31f29;
    --brand-navy:#1b2f55;
  }
  *{margin:0;padding:0;box-sizing:border-box}
  html,body{width:1200px;height:808px;overflow:hidden;background:var(--stage)}
  .canvas{position:relative;width:1200px;height:808px}
  .card{position:absolute;left:285px;width:630px;height:360px;overflow:hidden;border-radius:3px}
  .card--back{top:30px;background:var(--card-black);display:flex;align-items:center;justify-content:center}
  .card--front{top:418px;background:var(--white)}
  .back-name{font-family:"Archivo Black",sans-serif;font-size:58px;letter-spacing:-1px;color:var(--mark-grey);line-height:1}
  .front-shapes{position:absolute;inset:0}
  .company-name{position:absolute;right:30px;top:46px;font-family:"Archivo Black",sans-serif;font-size:38px;letter-spacing:-0.5px;color:var(--brand-red);line-height:1}
  .person{position:absolute;right:24px;top:112px;text-align:right}
  .person-name{font-family:"Archivo Black",sans-serif;font-size:26px;letter-spacing:1px;color:var(--brand-navy);line-height:1.1}
  .person-title{font-family:"Roboto Slab",serif;font-size:17px;color:var(--brand-red);margin-top:2px}
  .contact{position:absolute;left:36px;top:196px;list-style:none;font-family:"Roboto Slab",serif;font-size:15px;color:var(--white);line-height:1.5}
  .contact li{display:flex;align-items:flex-start;gap:10px;white-space:nowrap}
  .contact svg{width:15px;height:15px;margin-top:4px;flex:none;fill:var(--white)}
  .contact .spacer{width:15px;flex:none}
</style>
</head>
<body>
<main class="canvas">
  <section class="card card--back" aria-label="Card back">
    <span class="back-name">Veltrane Group</span>
  </section>

  <section class="card card--front" aria-label="Card front">
    <svg class="front-shapes" viewBox="0 0 630 360" width="630" height="360" aria-hidden="true">
      <polygon points="0,0 422,273 229,360 0,360" fill="var(--brand-red)"/>
      <polygon points="630,180 630,360 229,360" fill="var(--brand-navy)"/>
    </svg>

    <div class="company-name">Veltrane Group</div>

    <div class="person">
      <div class="person-name">ROHESH KAMDAR</div>
      <div class="person-title">President / CEO</div>
    </div>

    <ul class="contact">
      <li>
        <svg viewBox="0 0 16 16"><path d="M8 0a6 6 0 0 0-6 6c0 4.5 6 10 6 10s6-5.5 6-10a6 6 0 0 0-6-6zm0 8.5A2.5 2.5 0 1 1 8 3.5a2.5 2.5 0 0 1 0 5z"/></svg>
        <span>4180 Lindqvist Ave</span>
      </li>
      <li><span class="spacer"></span><span>Brennick, OH 44812</span></li>
      <li>
        <svg viewBox="0 0 16 16"><path d="M4 0h8a1.5 1.5 0 0 1 1.5 1.5v13A1.5 1.5 0 0 1 12 16H4a1.5 1.5 0 0 1-1.5-1.5v-13A1.5 1.5 0 0 1 4 0zm0 2v10h8V2zm4 11a1 1 0 1 0 0 2 1 1 0 0 0 0-2z"/></svg>
        <span>604.781.2249</span>
      </li>
      <li>
        <svg viewBox="0 0 16 16"><path d="M0 3h16v10H0zm1.5 1.3v.3L8 9l6.5-4.4v-.3zm0 2.1v5.1h13V6.4L8 10.8z"/></svg>
        <span>roheshkamdar@veltrane.com</span>
      </li>
      <li>
        <svg viewBox="0 0 16 16"><path d="M8 0a8 8 0 1 0 0 16A8 8 0 0 0 8 0zm0 1.5c.9 0 2 1.8 2.4 5.3H5.6C6 3.3 7.1 1.5 8 1.5zM1.6 8.2h2.6c0 1.6.2 3 .6 4.3A6.5 6.5 0 0 1 1.6 8.2zm0-1.4a6.5 6.5 0 0 1 3.2-4.3c-.4 1.2-.6 2.7-.7 4.3zm6.4 7.7c-.9 0-2-1.8-2.4-5.3h4.8c-.4 3.5-1.5 5.3-2.4 5.3zm3.2-2c.4-1.3.6-2.7.6-4.3h2.6a6.5 6.5 0 0 1-3.2 4.3zm.6-5.7c0-1.6-.2-3.1-.6-4.3a6.5 6.5 0 0 1 3.2 4.3z"/></svg>
        <span>www.veltrane.com</span>
      </li>
    </ul>
  </section>
</main>
</body>
</html>
```